Coupon/promo code site

I am looking for a one page website that will provide a list of coupon codes that are used at checkout when buying something online. The site will only have coupon codes for one online retailer. I would like this to be generic (i.e. not specific to any one retailer). I would like to have some interchangeable parts so that I could later customize the site so that it is specific to any given retailer.

I envision the site having a list of coupon codes with information about each code like when it expires and what it provides. For example there would be a: code, expiration date, short description or name, and a longer description (i.e. details).
Updates

Project Deadline Extended
Reason: I am going to submit a wire frame that provides a better idea of what I am looking for.

I have uploaded a wire frame that gives a more clear indication of what I am looking for.  Please see this before submitting designs.  If you have already submitted a design, please revise your design considering the wire frame I have provided.

Thanks,
Brent

Target Market(s)

Someone who is shopping online and searching for a specific retailers coupon codes

Industry/Entity Type

Coupon

Requirements
Must have
• I would like the site to have a white or light colored background.

I need a place or two where I can interchangeably place different retailers' logos.

The web page should have a title like, "[retailer's] online coupon code"

In addition to a list or table of coupon codes, there should below this be a list or table of special offers or sale items.

At the very bottom in a way that is not too noticeable, it should say, "This coupon site was created by Pelvo Deals."

There should be a section (probably on the right side) that allows a user to submit their email address to be notified in the future of specials/deals for this retailer.

There should be a nice looking link that goes to the online retailer's website.
Nice to have
• Example sites with a look and feel that I like are:

http://www.quorvane.com/
https://thebrattle.com/
http://www.plimworks.com

This is an example of a site with coupon codes for just one retailer. This site is a little too busy, but you get the idea:
www.makenforth.com/coupon-codes‎

```html
<!DOCTYPE html>
<html lang="en">
<head>
<meta charset="utf-8">
<title>Company Name Promo Codes</title>
<link href="https://fonts.googleapis.com/css2?family=Mulish:wght@700;800;900&family=Lato:wght@300;400;700&family=Arimo:wght@400;700&family=Oswald:wght@500;600&display=swap" rel="stylesheet">
<style>
:root{
  --blue:#0a8fd6;
  --blue-dark:#0774b3;
  --red:#e8262b;
  --ink:#333;
  --band:#929292;
  --panel:#e6e6e6;
  --pill:#555;
  --rule:#ddd;
  --footer:#e3e3e3;
  --art:#ece3da;
}
*{box-sizing:border-box;margin:0;padding:0}
html,body{width:784px;height:1200px;overflow:hidden;background:#fff}
body{position:relative;font-family:Arimo,Arial,sans-serif;color:var(--ink)}

.site-header{position:absolute;left:0;top:0;width:784px;height:84px;border-bottom:1px dashed #ccc}
.brand-name{position:absolute;left:20px;top:26px;font-family:Mulish,sans-serif;font-weight:800;font-size:24px;color:var(--ink)}
.page-title{position:absolute;left:226px;top:19px;font-family:Mulish,sans-serif;font-weight:900;font-size:33px;color:var(--blue);letter-spacing:1.1px;white-space:nowrap}

.hero{position:absolute;left:0;top:84px;width:784px;height:217px;border-bottom:1px dashed #ccc}
.hero-art{position:absolute;left:34px;top:8px;width:204px;height:208px;background:var(--art)}
.hero-text{position:absolute;left:266px;top:66px;font-family:Lato,sans-serif;font-weight:300;font-size:23.5px;line-height:29px;color:#222;letter-spacing:-.7px;white-space:nowrap}

.codes{position:absolute;left:5px;width:562px}
.codes.first{top:320px}
.codes.second{top:800px}
.band{height:29px;background:var(--band);color:#fff;font-family:Mulish,sans-serif;font-weight:800;font-size:15px;padding:6px 0 0 16px;letter-spacing:.3px}
.offer{position:relative;margin:0 26px 0 21px;height:104px;border-bottom:1px solid var(--rule)}
.offer:nth-of-type(1){height:118px}
.offer:nth-of-type(3){height:106px}
.offer-title{position:absolute;left:2px;top:9px;font-size:14.5px;font-weight:400;color:var(--blue);white-space:nowrap}
.offer-desc{position:absolute;left:2px;top:30px;font-size:9.6px;line-height:11.5px;color:#333;white-space:nowrap}
.code-label{position:absolute;left:317px;top:9px;font-size:14px;color:#333}
.code-pill{position:absolute;left:417px;top:8px;width:95px;height:22px;border-radius:8px;background:var(--pill)}
.expires{position:absolute;left:2px;top:76px;font-size:9.6px;color:var(--red)}
.shop-at{position:absolute;left:296px;top:76px;font-size:8px;color:#444}
.shop-at a{margin-left:4px;font-weight:700;color:#333;text-decoration:none}

.signup{position:absolute;left:574px;top:322px;width:197px;height:222px;background:var(--panel)}
.signup-head{position:absolute;left:0;top:3px;width:197px;height:73px;background:var(--blue);display:flex;align-items:center;padding-left:12px;gap:10px}
.signup-head h2{font-family:Oswald,sans-serif;font-weight:600;font-size:19px;line-height:23px;color:#fff}
.signup-copy{position:absolute;left:13px;top:92px;width:174px;text-align:center;font-size:9.6px;line-height:11.5px;color:#666}
.email{position:absolute;left:8px;top:151px;width:181px;height:20px;border:1px solid #ccc;border-radius:3px;background:#fff;font-size:8.5px;padding:5px 0 0 9px;color:#333}
.subscribe{position:absolute;left:10px;top:180px;width:85px;height:26px;border-radius:4px;background:linear-gradient(#2aa3e6,var(--blue-dark));color:#fff;font-family:Oswald,sans-serif;font-weight:500;font-size:14px;text-align:center;line-height:25px}

.site-footer{position:absolute;left:0;top:1102px;width:784px;height:98px;background:var(--footer);text-align:center}
.social{display:flex;justify-content:center;gap:6px;margin-top:19px}
.social span{width:23px;height:23px;border-radius:50%;background:#555}
.copyright{margin-top:14px;font-size:9.6px;color:#333}
.credit{margin-top:6px;font-size:8.8px;color:#888;letter-spacing:.3px}
</style>
</head>
<body>
<header class="site-header">
  <span class="brand-name">Codenook</span>
  <h1 class="page-title">Company Name PROMO CODES</h1>
</header>

<section class="hero">
  <div class="hero-art" role="img" aria-label="Illustration of a shopper holding scissors and a fan of coupons"></div>
  <p class="hero-text">Welcome to the Company Name promo page. Here<br>you will find the best and most up to date promo<br>codes available directly from Company Name</p>
</section>

<section class="codes first">
  <div class="band">featured promo codes</div>
  <article class="offer">
    <h3 class="offer-title">$51.26 Average savings on Brightmart.com</h3>
    <p class="offer-desc">Receive up to 60% off + Extra 20% off Select Jewelry &amp; Watches.</p>
    <span class="code-label">Coupon Code:</span><span class="code-pill"></span>
    <span class="expires">Offer Expires: Aug 24, 2013</span>
    <span class="shop-at">Use this code when shopping at : <a href="#">Brightmart.com</a></span>
  </article>
  <article class="offer">
    <h3 class="offer-title">Free Shipping</h3>
    <p class="offer-desc">Receive free shipping on orders over $50. The description<br>could wrap like this</p>
    <span class="code-label">Coupon Code:</span><span class="code-pill"></span>
    <span class="expires">Offer Expires: Aug 24, 2013</span>
    <span class="shop-at">Use this code when shopping at : <a href="#">Brightmart.com</a></span>
  </article>
  <article class="offer">
    <h3 class="offer-title">$51.26 Average savings on Brightmart.com</h3>
    <p class="offer-desc">Receive up to 60% off + Extra 20% off Select Jewelry &amp; Watches.</p>
    <span class="code-label">Coupon Code:</span><span class="code-pill"></span>
    <span class="expires">Offer Expires: Aug 24, 2013</span>
    <span class="shop-at">Use this code when shopping at : <a href="#">Brightmart.com</a></span>
  </article>
  <article class="offer">
    <h3 class="offer-title">Free Shipping</h3>
    <p class="offer-desc">Receive free shipping on orders over $50. The description<br>could wrap like this</p>
    <span class="code-label">Coupon Code:</span><span class="code-pill"></span>
    <span class="expires">Offer Expires: Aug 24, 2013</span>
    <span class="shop-at">Use this code when shopping at : <a href="#">Brightmart.com</a></span>
  </article>
</section>

<section class="codes second">
  <div class="band">featured promo codes</div>
  <article class="offer">
    <h3 class="offer-title">$51.26 Average savings on Brightmart.com</h3>
    <p class="offer-desc">Receive up to 60% off + Extra 20% off Select Jewelry &amp; Watches.</p>
    <span class="code-label">Coupon Code:</span><span class="code-pill"></span>
    <span class="expires">Offer Expires: Aug 24, 2013</span>
    <span class="shop-at">Use this code when shopping at : <a href="#">Brightmart.com</a></span>
  </article>
  <article class="offer">
    <h3 class="offer-title">Free Shipping</h3>
    <p class="offer-desc">Receive free shipping on orders over $50. The description<br>could wrap like this</p>
    <span class="code-label">Coupon Code:</span><span class="code-pill"></span>
    <span class="expires">Offer Expires: Aug 24, 2013</span>
    <span class="shop-at">Use this code when shopping at : <a href="#">Brightmart.com</a></span>
  </article>
</section>

<aside class="signup">
  <div class="signup-head">
    <svg width="54" height="46" viewBox="0 0 54 46" aria-hidden="true">
      <path d="M2 18 L27 2 L52 18 L52 44 L2 44 Z" fill="#fff"/>
      <path d="M2 18 L27 34 L52 18" fill="none" stroke="#0a8fd6" stroke-width="2.5"/>
      <path d="M2 44 L22 30 M52 44 L32 30" stroke="#0a8fd6" stroke-width="2.5"/>
      <rect x="19" y="12" width="16" height="2.5" fill="#0a8fd6"/>
      <rect x="19" y="17" width="16" height="2.5" fill="#0a8fd6"/>
    </svg>
    <h2>Never Miss<br>Another Deal!</h2>
  </div>
  <p class="signup-copy">Our promotions are updated frequently, so be sure to sign-up for our newsletter to receive notification of new promo codes and exclusive offers.</p>
  <div class="email">Enter Your Email Address Here</div>
  <div class="subscribe">Subscribe</div>
</aside>

<footer class="site-footer">
  <div class="social"><span></span><span></span><span></span><span></span><span></span></div>
  <p class="copyright">Copyright © 2013 codenook.com All rights reserved.</p>
  <p class="credit">This coupon site was created by Pelvo Deals</p>
</footer>
</body>
</html>
```